New Business Card Design for Manufacturing

We are an engineering/manufacturing company that offers Advanced machining/assembly/engineering services, as well as innovative products for the heavy duty engine cooling markets.

We are looking to get a new business card designed that is clean and modern looking, but still fits the wide range of technical/skilled work we do.

- We hope to use this design as the base for other design work in new Presentations, web, and print work.

Industry/Entity Type

Engineering

Contact Information for Business Card

Our preferred color of blue is (RGB) 22/71/159 but can vary slightly from that color. Our content will be our Logo and full company name (Vantrell Forge Works, Inc.), company address, name, job title, phone number with extension, cell number, fax number, website, and email address on the cards.
We'd like the full company name next to the logo, but we are open to other interpretations of that layout.
Preferably, we would like the back side to be clean with just our logo, and the front to contain all of the contact information.

Colors
2f74b4
0355a3
85abd2

Requirements
Must have
• - Logo, company name, needed content - We are open to interpretation beyond that.
• - Standard size business card.
• - Horizontal orientation.
• - Enough space for lengthy names / job titles (for example, a job title could read "Directory of Human Resources" or "V.P. of Governmental Affairs"). We need this to look clean, whether the title be short (CEO) or long (as described above).

```html
<!DOCTYPE html>
<html lang="en">
<head>
<meta charset="utf-8">
<title>Vantrell Forge Works — Business Card</title>
<link href="https://fonts.googleapis.com/css2?family=Roboto:wght@300;400;500;700&display=swap" rel="stylesheet">
<style>
  :root {
    --stage: #3b3b3d;
    --card-back: #7b8087;
    --card-front: #ffffff;
    --brand-blue: #16479f;
    --brand-mid: #2f74b4;
    --text-grey: #8a8d91;
    --text-dark: #55585c;
    --white: #ffffff;
  }
  * { box-sizing: border-box; margin: 0; padding: 0; }
  html, body { width: 1200px; height: 896px; overflow: hidden; }
  body {
    background: var(--stage);
    font-family: "Roboto", Arial, sans-serif;
    position: relative;
  }
  .card {
    position: absolute;
    width: 525px;
    height: 300px;
    border-radius: 4px;
    box-shadow: 0 14px 30px rgba(0,0,0,.45);
    overflow: hidden;
  }
  .card-back { left: 50px; top: 170px; background: var(--card-back); }
  .card-front { left: 625px; top: 426px; background: var(--card-front); }

  /* back side */
  .back-mark {
    position: absolute; left: 70px; top: 92px;
    display: flex; align-items: center; gap: 16px;
  }
  .mark-square { width: 46px; height: 46px; border: 5px solid var(--white); }
  .back-name {
    color: var(--white); font-weight: 700; font-size: 25px;
    line-height: 1.05; letter-spacing: .5px; text-transform: uppercase;
  }
  .back-tagline {
    position: absolute; left: 70px; top: 172px;
    color: var(--white); font-size: 14px; font-weight: 500;
    letter-spacing: 1px; text-transform: uppercase;
  }
  .back-web {
    position: absolute; right: 34px; bottom: 28px;
    color: var(--white); font-size: 15px; font-weight: 300; letter-spacing: .3px;
  }

  /* front side */
  .front-mark {
    position: absolute; left: 34px; top: 104px; width: 190px;
  }
  .front-name {
    color: var(--brand-mid); font-weight: 700; font-size: 22px;
    line-height: 1.08; text-transform: uppercase;
  }
  .front-tagline {
    margin-top: 8px; color: var(--text-grey); font-size: 11px;
    font-weight: 500; letter-spacing: .8px; text-transform: uppercase;
  }
  .divider {
    position: absolute; left: 242px; top: 46px;
    width: 1.5px; height: 208px; background: var(--brand-mid);
  }
  .contact { position: absolute; left: 262px; top: 48px; right: 20px; }
  .person {
    color: var(--brand-mid); font-size: 24px; font-weight: 400;
    letter-spacing: .5px; text-transform: uppercase;
  }
  .role { color: var(--text-grey); font-size: 13px; margin-top: 4px; }
  .address { color: var(--text-grey); font-size: 13px; line-height: 1.45; margin-top: 14px; }
  .lines { list-style: none; margin-top: 14px; }
  .lines li {
    display: flex; align-items: center; gap: 8px;
    color: var(--text-dark); font-size: 13px; line-height: 1.6;
  }
  .lines svg { width: 11px; height: 11px; fill: var(--brand-mid); flex: none; }
  .lines strong { color: var(--brand-mid); font-weight: 700; }
</style>
</head>
<body>
  <section class="card card-back" aria-label="Business card back">
    <div class="back-mark">
      <span class="mark-square"></span>
      <span class="back-name">Vantrell<br>Forge Works</span>
    </div>
    <p class="back-tagline">Shaping What Moves</p>
    <p class="back-web">www.vantrellforge.com</p>
  </section>

  <section class="card card-front" aria-label="Business card front">
    <div class="front-mark">
      <p class="front-name">Vantrell<br>Forge Works</p>
      <p class="front-tagline">Shaping What Moves</p>
    </div>
    <span class="divider"></span>
    <div class="contact">
      <p class="person">Maren Colfax</p>
      <p class="role">Directory of Human Resources</p>
      <p class="address">418 Harlow Ave., Ste. 210<br>Dayton, OH 45402 USA</p>
      <ul class="lines">
        <li><svg viewBox="0 0 12 12"><path d="M2.5 1 4.5 1 5.3 3.6 4 4.6C4.6 6 6 7.4 7.4 8L8.4 6.7 11 7.5 11 9.5C11 10.3 10.3 11 9.5 11 5 11 1 7 1 2.5 1 1.7 1.7 1 2.5 1Z"/></svg>(555) 214-0386</li>
        <li><svg viewBox="0 0 12 12"><path d="M1 2.5h10v7H1z M1.6 3 6 6.4 10.4 3" fill="none" stroke="#2f74b4" stroke-width="1.2"/></svg>info@vantrellforge.com</li>
        <li><svg viewBox="0 0 12 12"><circle cx="6" cy="6" r="5"/></svg>www.<strong>vantrellforge</strong>.com</li>
      </ul>
    </div>
  </section>
</body>
</html>
```